Mindfulness School for Children -- Business Cards

We're looking for business cards for our school directors and owners. We're a mindfulness school for children called little lanterns. Attached are our logos/icons.

```html
<!DOCTYPE html>
<html lang="en">
<head>
<meta charset="UTF-8">
<title>little lanterns — business cards</title>
<link href="https://fonts.googleapis.com/css2?family=Source+Sans+3:wght@400;600;700&display=swap" rel="stylesheet">
<style>
  :root {
    --backdrop: #2c2f37;
    --teal: #4a9cb1;
    --teal-deep: #2f7f95;
    --teal-soft: #7fb9c8;
    --paper: #eceef2;
    --ink: #2a2d33;
    --green: #6aad8e;
    --white: #f4f5f7;
  }
  * { box-sizing: border-box; margin: 0; padding: 0; }
  html, body {
    width: 1200px; height: 1000px; overflow: hidden;
    background: var(--backdrop);
    font-family: "Source Sans 3", sans-serif;
  }
  .card {
    position: absolute; left: 250px;
    width: 700px; height: 400px;
    overflow: hidden;
    box-shadow: 0 10px 24px rgba(0,0,0,.35);
  }
  .card--front { top: 80px; background: var(--teal); }
  .card--back { top: 520px; background: var(--paper); }

  .decor { position: absolute; top: 0; height: 100%; }
  .card--front .decor {
    right: 0; width: 250px;
    background: linear-gradient(120deg, var(--teal) 0%, var(--teal-soft) 45%, var(--white) 100%);
  }
  .card--back .decor {
    left: 0; width: 270px;
    background: linear-gradient(300deg, var(--paper) 0%, var(--teal-soft) 50%, var(--teal) 100%);
  }

  .brand {
    position: absolute;
    display: flex; align-items: center; gap: 12px;
    font-weight: 600; letter-spacing: .5px;
  }
  .brand__dot { width: 14px; height: 14px; border-radius: 50%; }
  .card--front .brand { left: 80px; top: 168px; font-size: 52px; color: var(--teal-deep); }
  .card--front .brand__dot { background: var(--teal-deep); }
  .card--back .brand { left: 330px; top: 58px; font-size: 42px; color: var(--teal); }
  .card--back .brand__dot { background: var(--teal); }

  .person {
    position: absolute; left: 330px; top: 140px;
    border-left: 5px solid var(--teal);
    padding-left: 14px;
  }
  .person__name { font-size: 22px; font-weight: 700; color: var(--teal); }
  .person__name .first { color: var(--green); }
  .person__role { font-size: 16px; color: var(--ink); margin-top: 2px; }

  .address {
    position: absolute; left: 330px; top: 218px;
    font-size: 15px; line-height: 1.3; color: var(--ink);
  }
  .contacts {
    position: absolute; left: 330px; top: 272px;
    list-style: none; font-size: 15px; color: var(--ink);
  }
  .contacts li { display: flex; align-items: center; gap: 10px; line-height: 1.55; }
  .contacts svg { width: 14px; height: 14px; flex: none; }
</style>
</head>
<body>

<section class="card card--front" aria-label="Business card front">
  <div class="brand"><span class="brand__dot"></span>little lanterns</div>
  <div class="decor" role="img" aria-label="Large decorative brand emblem area"></div>
</section>

<section class="card card--back" aria-label="Business card back">
  <div class="decor" role="img" aria-label="Large watercolour-style decorative brand emblem area"></div>
  <div class="brand"><span class="brand__dot"></span>little lanterns</div>

  <div class="person">
    <p class="person__name"><span class="first">Clara</span> Whitfield</p>
    <p class="person__role">Managing Director</p>
  </div>

  <p class="address">218 Willow Lane Fairbrook<br>OR 97402, United States</p>

  <ul class="contacts">
    <li>
      <svg viewBox="0 0 16 16" aria-hidden="true"><path fill="#4a9cb1" d="M4 1.5l2.3 3-1.4 1.6a8 8 0 0 0 5 5l1.6-1.4 3 2.3-1.3 2.3C7.5 14 2 8.5 1.7 2.8z"/></svg>
      (+1) 555.014.2290
    </li>
    <li>
      <svg viewBox="0 0 16 16" aria-hidden="true"><rect x="1" y="3" width="14" height="10" rx="1" fill="#4a9cb1"/><path d="M1.5 3.5L8 9l6.5-5.5" fill="none" stroke="#eceef2" stroke-width="1.4"/></svg>
      hello@littlelanterns.org
    </li>
    <li>
      <svg viewBox="0 0 16 16" aria-hidden="true"><circle cx="8" cy="8" r="7" fill="#4a9cb1"/><path d="M1 8h14M8 1c-3 3.5-3 10.5 0 14M8 1c3 3.5 3 10.5 0 14" fill="none" stroke="#eceef2" stroke-width="1"/></svg>
      www.littlelanterns.org
    </li>
  </ul>
</section>

</body>
</html>
```